Basic Commercial & Residential Real Estate Web Site

I need a basic website for a new real estate company that deals with both residential and commercial sales. It must be clean and professional. We sell homes, office buildings, farms, and ranches. It should feel crisp and clean.
I need a main page with my logo and links to commercial, residential, farm and land searches with contact data forms. Also incorporated would be a mls property search (IDX) form. I am in Northern California and the current site I posted is at www.tlvarden.com. I need the functionality of the links and the supporting pages. I do not have all the copy ready because I did not know what to expect.
Updates

Project Deadline Extended
Reason: I apologize, I am extremely busy and you all need more data to do a good job. All the designs are great so far and it is extremely difficult to choose at this point. I haven't given you enough data. I haver now uploaded some relevent photos (not very good) and edited the brief. I am looking for what I call the Landing or main page with some functionality built in to other pages which I also need. Example if you click on "Commercial" it should go to a page that discusses our commercial dept.......

I would like to thank all the designers for all their hard work and efforts, I wish I could reward you all.

Thanks again for your creative and professional designs.

Edwin

Target Market(s)

Corporate Execs for the Commercial Buildings
Homeowners/Families for the Homes and Farms
Upper end people for the land to build estates

Industry/Entity Type

Real Estate

Font styles to use
Sans Serif

Requirements
Must have
• Our Logo should be prominent, pronounced
Need contact data or button
Functional Page that links to other data pages
Must Have a "search for properties" feature
Must say "Commercial and Residential Representation"
Pictures of Commercial Building and Nice Home (Tradtional not contemporary)
Nice to have
• Individual Buttons or links to "Commercial, Residential, Farm/Ranch, Land"
Contact Data displayed
button that says "Maple Crest"-next to button is Maple Crest Logo-see www.maplecrest.bz
Links to "Buyers and "Sellers"
Links to Facebook, twitter,.....etc
Should not have
• 20+ story commercial buildings or ultra modern. See uploaded files of typical buildings for commercial.

```html
<!DOCTYPE html>
<html lang="en">
<head>
<meta charset="utf-8">
<title>Properties by Lumen — Commercial and Residential Representation</title>
<link rel="stylesheet" href="https://fonts.googleapis.com/css2?family=Open+Sans:wdth,wght@75..100,300..800&family=PT+Serif:wght@400&display=swap">
<style>
:root{
  --header-bg:#2b2b2b;
  --footer-bg:#2e2e2e;
  --bottom-bg:#202020;
  --page-bg:#f3f3f3;
  --white:#ffffff;
  --ink:#222222;
  --muted:#555555;
  --accent:#1f9ad6;
  --accent-dark:#0f6fa6;
  --olive:#6c7d12;
  --olive-light:#9aa83a;
  --field:#e1e1e1;
  --field-line:#b9b9b9;
  --rule:#d6d6d6;
  --card-band:#151515;
}
*{box-sizing:border-box;margin:0;padding:0}
html,body{width:1200px;height:2412px;overflow:hidden}
body{position:relative;background:var(--page-bg);font-family:"Open Sans",Arial,sans-serif;color:var(--ink)}
.abs{position:absolute}
a{color:inherit;text-decoration:none}

/* header */
.site-header{left:0;top:0;width:1200px;height:127px;background:var(--header-bg)}
.brand{left:100px;top:16px;color:var(--white);font-weight:300;line-height:1}
.brand-small{display:block;font-size:19px;letter-spacing:3px;margin-left:72px}
.brand-name{display:block;font-size:66px;letter-spacing:6px;margin-top:4px}
.account-links{right:100px;top:33px;font-size:13px;color:var(--olive)}
.account-links span{margin:0 6px;color:#8b8b8b}
.main-nav{left:560px;top:78px;display:flex;height:47px}
.main-nav a{color:var(--white);font-size:17px;line-height:47px;padding:0 15px}
.main-nav a.is-current{background:var(--white);color:var(--ink)}

/* hero */
.hero{left:0;top:127px;width:1200px;height:533px;background:linear-gradient(180deg,#bcc9cc 0%,#d6dbd6 35%,#a7a59c 62%,#6f6769 100%)}
.hero-caption{left:180px;top:272px;width:423px;height:225px;background:rgba(255,255,255,.38)}
.hero-kicker{left:213px;top:298px;font-size:40px;font-weight:300;color:#7c8c2a}
.hero-title{left:215px;top:330px;font-size:112px;font-weight:300;color:#1b1b1b;letter-spacing:-1px}
.arrow-btn{width:30px;height:30px;background:#111;display:flex;align-items:center;justify-content:center}

/* category cards */
.card{width:289px;height:363px;top:700px;background:var(--white);box-shadow:0 1px 4px rgba(0,0,0,.18)}
.card-photo{position:absolute;left:0;top:0;width:289px;height:200px}
.card-band{position:absolute;left:0;top:200px;width:289px;height:35px;background:var(--card-band);color:var(--accent);font-size:17px;font-weight:600;padding-left:18px;line-height:38px;font-stretch:85%}
.card-text{position:absolute;left:18px;top:254px;width:260px;font-size:12.5px;line-height:16px;color:var(--ink)}
.read-more{font-size:12.5px;color:var(--olive)}
.card .read-more{position:absolute;right:18px;top:328px}

/* section headings */
.section-title{font-size:27px;font-weight:700;font-stretch:75%;color:var(--accent);display:flex;align-items:center}
.section-title::after{content:"";display:block;height:2px;background:#5cbce8;margin-left:12px;flex:1}

.feature-photo{width:248px;height:158px}
.feature-text{left:373px;width:380px;font-size:13px;line-height:22px;color:var(--ink)}

/* sidebar */
.discussions{left:812px;top:1127px;width:290px;height:548px;background:#ececec;box-shadow:0 1px 4px rgba(0,0,0,.2)}
.discussions-head{position:absolute;left:10px;top:11px;width:270px;height:55px;background:#f1f1f1;border-bottom:1px solid #d0d0d0;font-family:"PT Serif",Georgia,serif;font-size:16px;letter-spacing:.5px;line-height:55px;padding-left:28px;color:#222}
.discussion{position:absolute;left:10px;width:270px;height:62px;border-bottom:1px solid #d9d9d9;font-size:12.5px;line-height:21px;padding:6px 0 0 57px}
.discussion:nth-child(odd){background:var(--white)}
.discussion:nth-child(even){background:#f2f2f2}
.discussion svg{position:absolute;left:20px;top:12px}
.discussion .by{color:var(--ink)}
.discussion .by b{font-weight:400;color:var(--olive)}
.discussion .date{position:absolute;left:155px;top:27px}
.view-all-posts{position:absolute;left:60px;top:523px;width:176px;height:25px;background:#3a3a3a;clip-path:polygon(4% 0,96% 0,100% 100%,0 100%);color:#3b86c6;font-size:12px;text-align:center;line-height:27px}

/* search */
.city-box{left:102px;top:1718px;width:313px;height:279px;background:var(--white);border:1px solid #9a9a9a}
.city-head{position:absolute;left:0;top:0;width:311px;height:35px;border-bottom:1px solid #9a9a9a;font-size:17px;line-height:34px;padding-left:22px}
.city-view-all{position:absolute;right:0;top:0;width:70px;height:35px;border-left:1px solid #9a9a9a;font-size:13px;text-align:center;line-height:35px}
.check-row{position:absolute;left:30px;display:flex;align-items:center;gap:10px;font-size:12.5px}
.field-label{font-size:13px;color:var(--ink)}
.field{background:var(--field);border:1px solid var(--field-line);height:29px;font-size:12px;line-height:27px;padding-left:10px;color:#222}
.field.num{text-align:right;padding-right:6px}
.search-btn{left:990px;top:1947px;width:112px;height:28px;border-radius:7px;background:linear-gradient(180deg,#2ea3dd,#0d6ea8);color:var(--white);font-size:12.5px;text-align:center;line-height:28px}

/* footer */
.site-footer{left:0;top:2020px;width:1200px;height:342px;background:var(--footer-bg);color:var(--white)}
.footer-tag{height:34px;background:var(--accent);color:var(--white);font-size:15px;line-height:34px;text-align:center}
.footer-list{list-style:none;font-size:12.5px;line-height:32px}
.footer-list li::before{content:"";display:inline-block;width:0;height:0;border-left:8px solid var(--white);border-top:5px solid transparent;border-bottom:5px solid transparent;margin-right:17px}
.footer-text{font-size:12.5px;line-height:22px;color:var(--white)}
.footer-text .link{color:var(--olive)}
.contact-line{display:flex;align-items:center;gap:8px;font-size:12.5px}
.social{display:flex;gap:10px}
.social span{width:20px;height:20px;border-radius:50%}
.bottom-bar{left:0;top:2362px;width:1200px;height:50px;background:var(--bottom-bg);color:#cfcfcf;font-size:12px;text-align:center;line-height:50px}
</style>
</head>
<body>

<header class="site-header abs">
  <div class="brand abs"><span class="brand-small">PROPERTIES BY</span><span class="brand-name">LUMEN</span></div>
  <div class="account-links abs">Welcome Guest <span>|</span><a href="#">Login</a><span>|</span><a href="#">Register FREE</a></div>
  <nav class="main-nav abs">
    <a href="#" class="is-current">HOME</a><a href="#">COMMERCIAL</a><a href="#">RESIDENTIAL</a><a href="#">FORE</a><a href="#">RENT</a><a href="#">CONTACT</a>
  </nav>
</header>

<section class="hero abs" role="img" aria-label="Street view of a white low-rise commercial office building with cars and pedestrians"></section>
<div class="hero-caption abs"></div>
<div class="hero-kicker abs">Lorem Ipsum</div>
<div class="hero-title abs">simply</div>
<a href="#" class="arrow-btn abs" style="left:102px;top:377px" aria-label="Previous slide"><svg width="10" height="14" viewBox="0 0 10 14"><path d="M8 1 2 7l6 6" fill="none" stroke="#fff" stroke-width="2.5"/></svg></a>
<a href="#" class="arrow-btn abs" style="left:1068px;top:377px" aria-label="Next slide"><svg width="10" height="14" viewBox="0 0 10 14"><path d="m2 1 6 6-6 6" fill="none" stroke="#fff" stroke-width="2.5"/></svg></a>

<!-- category cards -->
<article class="card abs" style="left:102px">
  <div class="card-photo" role="img" aria-label="Large traditional estate home beside a lake" style="background:linear-gradient(180deg,#6fa3dc 0%,#c9d4dc 45%,#8a9b8a 70%,#4e6e80 100%)"></div>
  <div class="card-band">COMMERCIAL</div>
  <p class="card-text">Lorem Ipsum is simply dummy text of the printing and typesetting<br>Lorem Ipsum is simply dummy text of the printing and typesetting</p>
  <a href="#" class="read-more">Read more.....</a>
</article>
<article class="card abs" style="left:460px">
  <div class="card-photo" role="img" aria-label="Brick office building entrance with a directory sign" style="background:linear-gradient(180deg,#c96a2e 0%,#9a4a26 45%,#5f4a3a 75%,#6a7a40 100%)"></div>
  <div class="card-band">RESIDENTIAL</div>
  <p class="card-text">Lorem Ipsum is simply dummy text of the printing and typesetting<br>Lorem Ipsum is simply dummy text of the printing and typesetting</p>
  <a href="#" class="read-more">Read more.....</a>
</article>
<article class="card abs" style="left:813px">
  <div class="card-photo" role="img" aria-label="Glass and brick corporate office building" style="background:linear-gradient(160deg,#e9eef2 0%,#6f8fa8 40%,#2c4a63 70%,#7a4a3a 100%)"></div>
  <div class="card-band">FARM</div>
  <p class="card-text">Lorem Ipsum is simply dummy text of the printing and typesetting<br>Lorem Ipsum is simply dummy text of the printing and typesetting</p>
  <a href="#" class="read-more">Read more.....</a>
</article>
<a href="#" class="arrow-btn abs" style="left:93px;top:807px" aria-label="Previous"><svg width="10" height="14" viewBox="0 0 10 14"><path d="M8 1 2 7l6 6" fill="none" stroke="#fff" stroke-width="2.5"/></svg></a>
<a href="#" class="arrow-btn abs" style="left:1080px;top:807px" aria-label="Next"><svg width="10" height="14" viewBox="0 0 10 14"><path d="m2 1 6 6-6 6" fill="none" stroke="#fff" stroke-width="2.5"/></svg></a>

<!-- latest work -->
<h2 class="section-title abs" style="left:100px;top:1103px;width:650px">LATEST WORK</h2>
<div class="feature-photo abs" style="left:102px;top:1172px" role="img" aria-label="Two-storey brick commercial building under a pale sky" style="background:#999"></div>
<div class="feature-photo abs" style="left:102px;top:1172px;background:linear-gradient(180deg,#c5d3e2 0%,#dfe5ea 45%,#9b5a3f 65%,#7c7f80 100%)"></div>
<p class="feature-text abs" style="top:1178px">Lorem Ipsum is simply dummy text of the printing and type-setting<br>&nbsp;Loremy text the printing and typesettingLoremy text<br>the printing and typesetting</p>
<a href="#" class="read-more abs" style="left:660px;top:1278px">Read more...</a>

<!-- services -->
<h2 class="section-title abs" style="left:100px;top:1405px;width:650px">OUR SERVICES</h2>
<div class="feature-photo abs" style="left:102px;top:1472px;background:linear-gradient(135deg,#f2f2f2 0%,#d8d2cc 45%,#6b7480 80%,#3c4450 100%)" role="img" aria-label="Smiling office team celebrating together"></div>
<p class="feature-text abs" style="top:1470px">Lorem Ipsum is simply dummy text of the printing and type-setting<br>&nbsp;Loremy text the printing and typesettingLoremy text<br>the printing and typesetting</p>
<a href="#" class="read-more abs" style="left:670px;top:1596px">Read more...</a>

<!-- discussions -->
<aside class="discussions abs">
  <div class="discussions-head">LATEST DISCUSSIONS:</div>
  <div>
    <div class="discussion" style="top:70px"><svg width="16" height="13" viewBox="0 0 16 13"><path d="M8 1C4 1 1 3 1 6s2 4 4 4.5L4 12l4-1.5c4 0 7-2 7-4.5S12 1 8 1z" fill="#666"/></svg>Lorem Ipsum is simply dummy<br><span class="by">by : <b>Ipsum</b></span><span class="date">26-03-2014</span></div>
    <div class="discussion" style="top:132px"><svg width="16" height="13" viewBox="0 0 16 13"><path d="M8 1C4 1 1 3 1 6s2 4 4 4.5L4 12l4-1.5c4 0 7-2 7-4.5S12 1 8 1z" fill="#666"/></svg>Lorem Ipsum is simply dummy<br><span class="by">by : <b>Ipsum</b></span><span class="date">26-03-2014</span></div>
    <div class="discussion" style="top:194px"><svg width="16" height="13" viewBox="0 0 16 13"><path d="M8 1C4 1 1 3 1 6s2 4 4 4.5L4 12l4-1.5c4 0 7-2 7-4.5S12 1 8 1z" fill="#666"/></svg>Lorem Ipsum is simply dummy<br><span class="by">by : <b>Ipsum</b></span><span class="date">26-03-2014</span></div>
    <div class="discussion" style="top:256px"><svg width="16" height="13" viewBox="0 0 16 13"><path d="M8 1C4 1 1 3 1 6s2 4 4 4.5L4 12l4-1.5c4 0 7-2 7-4.5S12 1 8 1z" fill="#666"/></svg>Lorem Ipsum is simply dummy<br><span class="by">by : <b>Ipsum</b></span><span class="date">26-03-2014</span></div>
    <div class="discussion" style="top:318px"><svg width="16" height="13" viewBox="0 0 16 13"><path d="M8 1C4 1 1 3 1 6s2 4 4 4.5L4 12l4-1.5c4 0 7-2 7-4.5S12 1 8 1z" fill="#666"/></svg>Lorem Ipsum is simply dummy<br><span class="by">by : <b>Ipsum</b></span><span class="date">26-03-2014</span></div>
    <div class="discussion" style="top:380px"><svg width="16" height="13" viewBox="0 0 16 13"><path d="M8 1C4 1 1 3 1 6s2 4 4 4.5L4 12l4-1.5c4 0 7-2 7-4.5S12 1 8 1z" fill="#666"/></svg>Lorem Ipsum is simply dummy<br><span class="by">by : <b>Ipsum</b></span><span class="date">26-03-2014</span></div>
    <div class="discussion" style="top:442px"><svg width="16" height="13" viewBox="0 0 16 13"><path d="M8 1C4 1 1 3 1 6s2 4 4 4.5L4 12l4-1.5c4 0 7-2 7-4.5S12 1 8 1z" fill="#666"/></svg>Lorem Ipsum is simply dummy<br><span class="by">by : <b>Ipsum</b></span><span class="date">26-03-2014</span></div>
  </div>
  <a href="#" class="view-all-posts">VIEW ALL POSTS</a>
</aside>

<!-- real estate search -->
<h2 class="section-title abs" style="left:105px;top:1658px;width:645px;font-size:23px;font-weight:600;font-stretch:100%">REAL ESTATE SEARCH</h2>
<form class="property-search">
  <div class="city-box abs">
    <div class="city-head">City Zip</div>
    <div class="city-view-all">VIEW ALL</div>
    <div class="check-row" style="top:58px"><svg width="16" height="13" viewBox="0 0 16 13"><rect x="0.5" y="2.5" width="10" height="10" fill="#ddd" stroke="#888"/><path d="M2 7l3 3 9-9" fill="none" stroke="#444" stroke-width="2"/></svg>El Dorado</div>
    <div class="check-row" style="top:82px"><svg width="16" height="13" viewBox="0 0 16 13"><rect x="0.5" y="2.5" width="10" height="10" fill="#ddd" stroke="#888"/><path d="M2 7l3 3 9-9" fill="none" stroke="#444" stroke-width="2"/></svg>El Dorado Hills</div>
    <div class="check-row" style="top:106px"><svg width="16" height="13" viewBox="0 0 16 13"><rect x="0.5" y="2.5" width="10" height="10" fill="#ddd" stroke="#888"/><path d="M2 7l3 3 9-9" fill="none" stroke="#444" stroke-width="2"/></svg>Cameron Park</div>
  </div>

  <div class="field-label abs" style="left:515px;top:1714px;font-size:17px">Property Type</div>
  <div class="field abs" style="left:512px;top:1745px;width:325px;height:32px;line-height:30px;font-size:13px;padding-left:20px;border:none">House Only</div>

  <div class="field-label abs" style="left:513px;top:1792px;font-size:12px">Min Price</div>
  <div class="field-label abs" style="left:725px;top:1792px;font-size:12px">Max. Price</div>
  <div class="field-label abs" style="left:935px;top:1792px;font-size:12px">Min. Sq. Ft.</div>
  <div class="field-label abs" style="left:513px;top:1824px;font-weight:700;font-size:12px">$</div>
  <div class="field num abs" style="left:528px;top:1818px;width:132px">0000000</div>
  <div class="field-label abs" style="left:725px;top:1824px;font-weight:700;font-size:12px">$</div>
  <div class="field num abs" style="left:740px;top:1818px;width:132px">0000000</div>
  <div class="field abs" style="left:935px;top:1818px;width:165px"></div>

  <div class="field-label abs" style="left:513px;top:1867px;font-size:12px">Bedrooms</div>
  <div class="field-label abs" style="left:725px;top:1867px;font-size:12px">Bathrooms</div>
  <div class="field-label abs" style="left:935px;top:1867px;font-size:12px">Min.Acres</div>
  <div class="field abs" style="left:513px;top:1893px;width:149px">Any</div>
  <div class="field abs" style="left:725px;top:1893px;width:148px">Any</div>
  <div class="field abs" style="left:935px;top:1893px;width:165px"></div>

  <div class="check-row" style="left:512px;top:1952px"><svg width="16" height="13" viewBox="0 0 16 13"><path d="M2 11a6 6 0 0 1 11-5" fill="none" stroke="#777" stroke-width="1.5"/></svg>Cameron Park</div>
  <div class="check-row" style="left:512px;top:1985px"><svg width="16" height="13" viewBox="0 0 16 13"><rect x="0.5" y="2.5" width="10" height="10" fill="#ddd" stroke="#888"/><path d="M2 7l3 3 9-9" fill="none" stroke="#444" stroke-width="2"/></svg>Cameron Park</div>
  <a href="#" class="search-btn abs">SEARCH</a>
</form>

<!-- footer -->
<footer class="site-footer abs">
  <div class="footer-tag abs" style="left:102px;top:70px;width:122px">Quick link</div>
  <ul class="footer-list abs" style="left:102px;top:121px">
    <li>Home</li><li>Commercial</li><li>Residential</li><li>Fore</li><li>Rent</li><li>Contact</li>
  </ul>
  <div class="footer-tag abs" style="left:350px;top:70px;width:122px">About Us</div>
  <ul class="footer-list abs" style="left:350px;top:121px">
    <li>Lorem Ipsum</li><li>Lorem Ipsum</li><li>Lorem Ipsum</li><li>Lorem Ipsum</li><li>Lorem Ipsum</li><li>Lorem Ipsum</li>
  </ul>
  <div class="footer-tag abs" style="left:582px;top:70px;width:105px">Blog</div>
  <p class="footer-text abs" style="left:580px;top:121px;width:250px">Lorem Ipsum is simply dummy text<br>of the printing and typesetting<br><span class="link">industry's standard industry's stan-</span></p>
  <p class="footer-text abs" style="left:580px;top:222px;width:250px">Lorem Ipsum is simply dummy text<br>of the printing and typesetting<br><span class="link">industry's standard dard</span></p>
  <div class="footer-tag abs" style="left:890px;top:73px;width:120px">Contact Us</div>
  <p class="footer-text abs" style="left:890px;top:121px;width:250px">Lorem Ipsum is simply dummy text<br>of the printing and typesetting<br>of the printing and typesetting</p>
  <div class="contact-line abs" style="left:890px;top:205px"><svg width="12" height="14" viewBox="0 0 12 14"><path d="M3 1c-2 1-2 3-1 6s3 5 5 6c1 0 2-1 2-2l-2-2-1 1C5 9 4 7 4 6l1-1-1-3z" fill="#fff"/></svg>: +1-0123-456-789</div>
  <div class="contact-line abs" style="left:890px;top:233px"><svg width="18" height="12" viewBox="0 0 18 12"><rect x="0.5" y="0.5" width="17" height="11" fill="none" stroke="#fff"/><path d="M1 1l8 6 8-6" fill="none" stroke="#fff"/></svg>: &nbsp;lumenmail.com</div>
  <div class="social abs" style="left:890px;top:282px">
    <span style="background:#3b5d9c" aria-label="Social link"></span>
    <span style="background:#1b9ed7" aria-label="Social link"></span>
    <span style="background:#1a6fa8" aria-label="Social link"></span>
    <span style="background:#d6483a" aria-label="Social link"></span>
  </div>
</footer>
<div class="bottom-bar abs">Copyright © 2014 . All rights reserved.</div>

</body>
</html>
```